Paws of Kindness Comfort & Dog Training

I have a dual themed business. I am a nationally recognized dog trainer for NCR (National Canine Registry) and Tail Allies (Pet Therapy). One side of my business card will need to address my pet therapy ministry called "Paws of Kindness Comfort". We visit almost 1,000 people a month bringing emotionally uplifting happy visits for nursing homes, veterans hospitals, hospice care, surgery recovery, school systems, and libraries, etc. In addition to emotionally positive effects, pet therapy also helps with anxiety, mobility, regulating blood pressure, and many more advantages. I've attached 2 graphics that are connected with this ministry; #1 paw print inside ribbon heart, #2 clasping hands sketch. The story behind the clasping hands is that it is an actual picture of my hand holding my mother's hand on her death bed (with a sketch filter used). My mother lived in a different state than I live in, and I had wished she had pet therapy available to her in her last months of life. They would have provided some bright moments to her difficult days. So, I vowed that although I was not able to help my own mother, I could train my own dog to reach out to hundreds of people in the community I live in. I have continued to live up to that vow, and have gone on to become a national trainer for other people who would like to train their pets to do the same thing.SIDE TWO of my business card will be announcing that I am a dog trainer for puppies, basic obedience, pet therapy, ESA (emotional support animals), and service dogs. Additionally, I offer canine body language training, dog agility training, and cognitive training. I have also attached two graphics for this side: #1 NCR logo, #2 Tail Allies Evaluation

Target Market(s)

Industry/Entity Type

Dog Training

Contact Information for Business Card

I'm looking for a designer who is good with color scheme & fonts.
2-sided card
one side for pet therapy
one side for dog training

Logo Text

Paws of KindnessComfort

Font styles to use
Sans Serif
Decorative

Colors

Designer to choose colors to be used in the design.

Requirements
Must have
• -Contact information: Marla Quinby (555) 926-3140
• - Contact information for online: Paws of Kindness Comfort (Facebook, Instagram & Twitter)
• - Graphics for pet therapy: clasping hands
• - Graphics for dog training: NCR Canine Fine Neighbor, Tail Allies
• - List of dog training classes I offer: Basic Obedience, NCR Canine Fine Neighbor, NCR B.R.I.G.H.T. Puppy, Pet Therapy training, ESA (Emotional Support Animal), Service Dog training, Canine Body Language, Dog Agility, Cognitive Training, Dog Trick Training
Nice to have
• appealing graphic for dog training school
• Titles in decorative font (but still easy to read) & detail info in very easy to read font

```html
<!DOCTYPE html>
<html lang="en">
<head>
<meta charset="utf-8">
<title>Paws of Kindness Comfort – Business Card</title>
<link rel="stylesheet" href="https://fonts.googleapis.com/css2?family=Oswald:wght@600&family=Open+Sans:wght@400;600;700&family=Pinyon+Script&display=swap">
<style>
  :root {
    --bg: #e9e4dc;
    --yellow: #f1e233;
    --ink: #1b1b17;
    --blue: #1f6fc0;
    --dark: #221c13;
    --orange: #e0672a;
    --white: #f4f1ea;
    --sketch-light: #cdbf9f;
    --sketch-dark: #3a3123;
  }
  * { box-sizing: border-box; margin: 0; padding: 0; }
  html, body { width: 1200px; height: 1200px; overflow: hidden; }
  body {
    background: var(--bg);
    display: flex; align-items: center; justify-content: center; gap: 60px;
    font-family: "Open Sans", sans-serif;
  }
  .card { box-shadow: 0 6px 18px rgba(0,0,0,.25); position: relative; overflow: hidden; }

  /* Training side */
  .card--training {
    width: 640px; height: 366px; background: var(--yellow); color: var(--ink);
    display: flex; flex-direction: column; align-items: center; text-align: center;
    padding: 26px 30px 18px;
  }
  .trainer-name { font-family: "Oswald", sans-serif; font-weight: 600; font-size: 32px; letter-spacing: 1px; line-height: 1.1; }
  .trainer-role { color: var(--blue); font-size: 15px; font-weight: 600; letter-spacing: .5px; margin-bottom: 6px; }
  .contact-icons { display: flex; gap: 6px; margin-bottom: 4px; }
  .contact-line { font-size: 15px; line-height: 1.35; }
  .provide-title { color: var(--blue); font-weight: 700; font-size: 18px; margin: 8px 0 4px; letter-spacing: .5px; }
  .class-list { font-size: 13.5px; line-height: 1.45; }
  .partner-row { display: flex; align-items: center; gap: 26px; margin-top: auto; }
  .badge { width: 44px; height: 44px; border-radius: 50%; background: var(--blue); }
  .partner-mark { display: flex; align-items: center; gap: 8px; }
  .partner-dot { width: 22px; height: 22px; border-radius: 50%; background: #8a1f3a; }
  .partner-text { display: flex; flex-direction: column; align-items: flex-start; }
  .partner-name { font-weight: 700; font-size: 16px; color: #8a1f3a; line-height: 1; }
  .partner-tag { font-size: 8px; color: #8a1f3a; }

  /* Therapy side */
  .card--therapy {
    width: 366px; height: 640px; background: var(--dark); color: var(--white);
    display: flex; flex-direction: column; align-items: center;
    padding: 0 16px;
  }
  .therapy-title {
    font-family: "Pinyon Script", cursive; font-weight: 400; color: var(--orange);
    font-size: 31px; line-height: 1.2; margin-top: 36px; white-space: nowrap; text-align: center;
  }
  .find-us { font-weight: 700; font-size: 14px; margin-top: 18px; }
  .social-list { list-style: none; font-size: 14px; line-height: 1.45; margin-top: 2px; }
  .social-list li { display: flex; align-items: center; gap: 6px; }
  .social-dot { width: 10px; height: 10px; background: var(--orange); flex-shrink: 0; }
  .hands-art {
    width: 220px; height: 330px; margin-top: 22px; margin-right: 50px;
    background: radial-gradient(ellipse at 50% 45%, var(--sketch-light) 0%, #a89878 45%, var(--sketch-dark) 85%, transparent 100%);
    border-radius: 40% 40% 10% 10%;
  }
  .therapy-mark {
    position: absolute; right: 16px; bottom: 20px;
    display: flex; align-items: center; gap: 6px;
    color: var(--orange); font-size: 12px; font-weight: 600;
  }
  .therapy-mark .circle { width: 16px; height: 16px; border-radius: 50%; background: var(--orange); }
</style>
</head>
<body>

  <section class="card card--training">
    <h1 class="trainer-name">MARLA QUINBY</h1>
    <p class="trainer-role">DOG TRAINER</p>
    <div class="contact-icons">
      <svg width="18" height="18" viewBox="0 0 18 18" aria-hidden="true"><circle cx="9" cy="9" r="9" fill="var(--blue)"/><path d="M6 5 l2 0 l1 2.5 l-1.2 1 a6 6 0 0 0 2.7 2.7 l1-1.2 l2.5 1 l0 2 a1 1 0 0 1 -1 1 a8 8 0 0 1 -8 -8 a1 1 0 0 1 1 -1z" fill="#fff"/></svg>
      <svg width="18" height="18" viewBox="0 0 18 18" aria-hidden="true"><circle cx="9" cy="9" r="9" fill="var(--blue)"/><rect x="4.5" y="6" width="9" height="6.5" fill="#fff"/><path d="M4.5 6 L9 9.5 L13.5 6" stroke="var(--blue)" fill="none"/></svg>
    </div>
    <p class="contact-line">+(555) 926-3140</p>
    <p class="contact-line">pawsofkindnesscomfort@kindmail.net</p>
    <h2 class="provide-title">WE PROVIDE :</h2>
    <p class="class-list">
      Basic Obedience, NCR Canine Fine Neighbor, NCR B.R.I.G.H.T. Puppy, Pet Therapy training,<br>
      ESA (Emotional Support Animal), Canine Body Language, Service Dog training,<br>
      Canine Body Language, Dog Agility, Cognitive Training, Dog Trick Training
    </p>
    <div class="partner-row">
      <div class="badge" role="img" aria-label="Evaluator badge"></div>
      <div class="partner-mark">
        <span class="partner-dot"></span>
        <div class="partner-text">
          <span class="partner-name">Tail Allies</span>
          <span class="partner-tag">Kind visits, better days</span>
        </div>
      </div>
    </div>
  </section>

  <section class="card card--therapy">
    <h1 class="therapy-title">Paws of Kindness Comfort</h1>
    <p class="find-us">FIND US :</p>
    <ul class="social-list">
      <li><span class="social-dot"></span>PawsOfKindnessComfort</li>
      <li><span class="social-dot"></span>@PawsofKindnes</li>
      <li><span class="social-dot"></span>@PawsofKindnes</li>
    </ul>
    <div class="hands-art" role="img" aria-label="Sketch of two clasped hands"></div>
    <div class="therapy-mark"><span class="circle"></span>Paws of Kindness</div>
  </section>

</body>
</html>
```